Create a memorable Web Design for real estate branding

we are a Minnepolis brokerage and boutique housing specialist with over 27 years of experience in the Global furnished housing industry, servicing the Greater Los Angeles area. Specializing in “warm environments” we offer a customized approach to satisfying our guests and client’s needs by offering a wide array of options in highly desirable areas. Additionally, Lantern Dwelling Partners offers assistance and expertise to home buyers, sellers and investors.

Industry/Entity Type

Real Estate

Number of Pages Required

1 page

Font styles to use
Serif
Sans Serif
Decorative

```html
<!DOCTYPE html>
<html lang="en">
<head>
<meta charset="utf-8">
<title>Lantern Dwelling Real Estate</title>
<link href="https://fonts.googleapis.com/css2?family=Montserrat:wght@400;500;600;700&family=Open+Sans:wght@400;600&display=swap" rel="stylesheet">
<style>
:root{
  --teal:#13a888;
  --teal-dark:#0f8f74;
  --lime:#a8dc4a;
  --lime-dark:#93c93a;
  --ink:#2b2b2b;
  --text:#555;
  --muted:#8a8a8a;
  --grey-bg:#ececec;
  --white:#fff;
}
*{box-sizing:border-box;margin:0;padding:0}
html,body{width:1200px;height:2946px;overflow:hidden}
body{font-family:"Open Sans",Arial,sans-serif;color:var(--text);background:var(--white);position:relative}
h1,h2,h3,h4,.nav,.logo{font-family:"Montserrat",Arial,sans-serif}

/* header */
.site-header{position:absolute;top:0;left:0;width:1200px;height:128px;border-top:4px solid var(--teal);background:var(--white)}
.logo{position:absolute;left:130px;top:44px;display:flex;align-items:center;gap:12px;font-weight:700;font-size:26px;line-height:34px;color:var(--teal);white-space:nowrap}
.logo .mark{width:22px;height:22px;background:var(--lime);border-radius:50%}
.nav{position:absolute;left:461px;top:58px;width:606px;display:flex;justify-content:space-between;font-size:11px;font-weight:600;color:#333;white-space:nowrap}
.nav .active{color:var(--teal)}

/* hero */
.hero{position:absolute;top:128px;left:0;width:1200px;height:422px;background:linear-gradient(180deg,#5b6d84 0%,#7f8da0 40%,#8c8a7a 80%,#6d6b5e 100%)}
.hero-title{position:absolute;top:100px;width:100%;text-align:center;color:var(--white);font-size:32px;font-weight:500;letter-spacing:1px}
.search-panel{position:absolute;left:198px;top:182px;width:802px;height:126px;background:rgba(19,168,136,.82);padding:22px 18px}
.search-panel h2{color:var(--white);font-size:19px;font-weight:500;margin-bottom:16px;letter-spacing:.5px}
.search-row{display:flex;gap:8px}
.field{height:40px;background:var(--white);font-size:12px;color:#555;padding:0 12px;display:flex;align-items:center;justify-content:space-between;width:240px}
.btn-search{width:98px;height:40px;background:var(--lime);color:var(--white);font-size:11px;display:flex;align-items:center;justify-content:center;font-weight:600}
.hero-arrow{position:absolute;top:210px;width:16px;height:30px}

/* services */
.services{position:absolute;top:550px;left:0;width:1200px;height:432px}
.service{position:absolute;top:70px;width:320px;text-align:center}
.service h3{font-size:19px;font-weight:500;color:var(--ink);margin:40px 0 20px;letter-spacing:.5px}
.service p{font-size:11.5px;line-height:20px;color:#444;width:270px;margin:0 auto}
.service .more{display:block;font-size:11px;margin-top:22px;color:#444}
.hex{width:120px;height:136px;margin:0 auto;display:block}

/* about */
.about{position:absolute;top:982px;left:0;width:1200px;height:570px}
.about-photo{position:absolute;right:0;top:0;width:760px;height:570px;background:linear-gradient(135deg,#f2f2f0 0%,#d9dcdd 45%,#b9a69a 70%,#e9e4df 100%)}
.about-panel{position:absolute;left:0;top:0;width:720px;height:570px}
.about-content{position:absolute;left:134px;top:78px;width:500px;color:var(--white)}
.about-content h2{font-size:28px;font-weight:500;margin-bottom:20px}
.about-content > p{font-size:11px;line-height:19px}
.feature{display:flex;align-items:center;gap:16px;margin-top:36px}
.feature .dot{width:72px;height:72px;border-radius:50%;background:var(--lime);flex:none;display:flex;align-items:center;justify-content:center}
.feature h4{font-size:18px;font-weight:500;margin-bottom:8px}
.feature p{font-size:11px;line-height:19px}

/* featured */
.featured{position:absolute;top:1552px;left:0;width:1200px;height:605px;background:var(--grey-bg)}
.section-head{position:absolute;width:100%;text-align:center;font-size:19px;font-weight:500;color:var(--ink);letter-spacing:.5px;font-family:"Montserrat",Arial,sans-serif}
.section-head .chev{display:inline-block;margin:0 40px;color:#555}
.card{position:absolute;top:145px;width:284px;height:371px;background:var(--white);box-shadow:0 2px 6px rgba(0,0,0,.08)}
.card-img{height:173px;position:relative}
.tag{position:absolute;right:0;bottom:0;width:104px;height:34px;color:var(--white);font-size:14px;display:flex;align-items:center;justify-content:center}
.tag.sale{background:var(--teal)}
.tag.rent{background:var(--lime)}
.card-body{padding:18px 18px 0}
.card h3{font-size:14px;font-weight:500;color:var(--ink)}
.price{font-size:15px;font-weight:600;color:var(--teal);margin:6px 0 20px;font-family:"Montserrat",Arial,sans-serif}
.spec{display:flex;align-items:center;font-size:12.5px;color:#333;height:35px}
.spec svg{width:18px;height:16px;margin-right:16px}
.spec b{margin-left:auto;color:var(--teal);font-weight:600}

/* testimonials */
.testimonials{position:absolute;top:2157px;left:0;width:1200px;height:322px;background:var(--lime);color:var(--white)}
.testimonials .section-head{color:var(--white);top:56px}
.testimonials .section-head .chev{color:var(--white)}
.quote{position:absolute;top:118px;width:100%;text-align:center;font-size:11px;line-height:20px}
.avatar{position:absolute;top:170px;left:564px;width:72px;height:72px;border-radius:50%;background:linear-gradient(160deg,#8a5a3c,#d9a683);border:3px solid var(--white)}
.client{position:absolute;top:266px;width:100%;text-align:center;font-size:12px}

/* contact */
.contact{position:absolute;top:2479px;left:0;width:1200px;height:467px;background:linear-gradient(180deg,#e9eaec 0%,#dcdee1 60%,#e4e5e7 100%)}
.contact h2{position:absolute;top:46px;font-size:17px;font-weight:500;color:var(--ink)}
.info{position:absolute;left:130px;display:flex;gap:14px}
.info .pin{width:52px;height:52px;border-radius:50%;background:var(--lime);flex:none;display:flex;align-items:center;justify-content:center}
.info h4{font-size:19px;font-weight:500;color:var(--ink);margin:2px 0 4px}
.info p{font-size:10.5px;line-height:17px;color:#333;width:300px}
.input{position:absolute;background:var(--white);border:1px solid #d2d2d2;font-size:10px;color:#333;padding:10px 12px}
.btn-submit{position:absolute;left:972px;top:304px;width:96px;height:32px;background:var(--lime);color:var(--white);font-size:12px;display:flex;align-items:center;justify-content:center}
.socials{position:absolute;left:534px;top:360px;display:flex;gap:12px}
.socials span{width:38px;height:38px;background:var(--teal);display:block;clip-path:polygon(50% 0,100% 25%,100% 75%,50% 100%,0 75%,0 25%)}
.copyright{position:absolute;top:432px;width:100%;text-align:center;font-size:10px;color:#444}
</style>
</head>
<body>

<header class="site-header">
  <div class="logo"><span class="mark"></span>Lantern Dwelling</div>
  <nav class="nav">
    <span class="active">HOME</span><span>ABOUT</span><span>LISTINGS</span><span>SERVICES</span><span>AGENTS</span><span>GALLERY</span><span>NEWS</span><span>CONTACT US</span>
  </nav>
</header>

<section class="hero" role="img" aria-label="City skyline with downtown towers under a cloudy sky">
  <h1 class="hero-title">SPECIALIZING IN “WARM ENVIRONMENTS”</h1>
  <svg class="hero-arrow" style="left:134px" viewBox="0 0 16 30"><polyline points="13,3 3,15 13,27" fill="none" stroke="#fff" stroke-width="3"/></svg>
  <svg class="hero-arrow" style="right:134px" viewBox="0 0 16 30"><polyline points="3,3 13,15 3,27" fill="none" stroke="#fff" stroke-width="3"/></svg>
  <div class="search-panel">
    <h2>FIND YOUR DREAM HOME</h2>
    <div class="search-row">
      <div class="field">Property Type <span>▤</span></div>
      <div class="field">Loaction <span>⌖</span></div>
      <div class="field">Price Range <span>◆</span></div>
      <div class="btn-search">SEARCH</div>
    </div>
  </div>
</section>

<section class="services">
  <div class="service" style="left:97px">
    <svg class="hex" viewBox="0 0 120 136"><polygon points="60,0 120,34 120,102 60,136 0,102 0,34" fill="#a8dc4a"/><path d="M38 72 L60 52 L78 68 M44 68 V90 H62" fill="none" stroke="#fff" stroke-width="4"/><circle cx="76" cy="82" r="13" fill="none" stroke="#fff" stroke-width="4"/><text x="76" y="88" font-size="16" fill="#fff" text-anchor="middle" font-family="Montserrat,sans-serif" font-weight="700">$</text></svg>
    <h3>REAL ESTATE</h3>
    <p>Lorem ipsum dolor sit amet, consectetur adipiscing elit, sed do eiusmod tempor incididunt ut labore et dolore magna aliqua.</p>
    <span class="more">Read More ▸</span>
  </div>
  <div class="service" style="left:439px">
    <svg class="hex" viewBox="0 0 120 136"><polygon points="60,0 120,34 120,102 60,136 0,102 0,34" fill="#13a888"/><rect x="36" y="60" width="18" height="24" rx="3" fill="none" stroke="#fff" stroke-width="4"/><rect x="62" y="48" width="22" height="40" rx="4" fill="none" stroke="#fff" stroke-width="4"/><path d="M62 64 H84" stroke="#fff" stroke-width="4"/></svg>
    <h3>BROKERAGE</h3>
    <p>Lorem ipsum dolor sit amet, consectetur adipiscing elit, sed do eiusmod tempor incididunt ut labore et dolore magna aliqua.</p>
    <span class="more">Read More ▸</span>
  </div>
  <div class="service" style="left:781px">
    <svg class="hex" viewBox="0 0 120 136"><polygon points="60,0 120,34 120,102 60,136 0,102 0,34" fill="#13a888"/><path d="M36 50 H84 L88 64 H32 Z" fill="#fff"/><rect x="38" y="64" width="44" height="28" fill="none" stroke="#fff" stroke-width="4"/><rect x="52" y="72" width="16" height="20" fill="#fff"/></svg>
    <h3>BOUTIQUE HOUSING</h3>
    <p>Lorem ipsum dolor sit amet, consectetur adipiscing elit, sed do eiusmod tempor incididunt ut labore et dolore magna aliqua.</p>
    <span class="more">Read More ▸</span>
  </div>
</section>

<section class="about">
  <div class="about-photo" role="img" aria-label="Couple reviewing a home model and laptop with an agent in a bright office"></div>
  <svg class="about-panel" viewBox="0 0 720 570" preserveAspectRatio="none"><polygon points="0,0 560,0 716,282 560,570 0,570" fill="#13a888"/></svg>
  <div class="about-content">
    <h2>ABOUT US</h2>
    <p>Aliquam dui justo, feugiat eu ligula at, posuere cursus enim. Fusce dictum egestas sem eu convallis. Suspendisse sapien turpis, iaculis eu congue at, tristique facilisis sapien. Vivamus sit amet cursus orci. Duis tempor vitae felis sed volutpat</p>
    <div class="feature"><span class="dot"><svg width="26" height="26" viewBox="0 0 26 26"><path d="M5 4 H20 V22 H7 Q5 22 5 20 Z" fill="#fff"/><path d="M8 8 H17" stroke="#a8dc4a" stroke-width="2"/></svg></span><div><h4>GUIDANCE</h4><p>At vero eos et accusamus et iusto odio dignissimos<br>ducimus qui blanditiis</p></div></div>
    <div class="feature"><span class="dot"><svg width="26" height="26" viewBox="0 0 26 26"><rect x="3" y="11" width="5" height="11" fill="#fff"/><path d="M10 11 L14 3 Q17 3 16 8 H22 Q24 9 23 12 L20 22 H10 Z" fill="#fff"/></svg></span><div><h4>ADVERTISE</h4><p>At vero eos et accusamus et iusto odio dignissimos<br>ducimus qui blanditiis</p></div></div>
    <div class="feature"><span class="dot"><svg width="26" height="26" viewBox="0 0 26 26"><path d="M6 3 H16 L21 8 V23 H6 Z" fill="none" stroke="#fff" stroke-width="2"/><path d="M9 12 H18 M9 16 H18 M9 20 H15" stroke="#fff" stroke-width="2"/></svg></span><div><h4>LISTING</h4><p>At vero eos et accusamus et iusto odio dignissimos<br>ducimus qui blanditiis</p></div></div>
  </div>
</section>

<section class="featured">
  <h2 class="section-head" style="top:72px"><span class="chev">‹</span>FEATURED PROPERTIES<span class="chev">›</span></h2>

  <article class="card" style="left:132px">
    <div class="card-img" role="img" aria-label="Modern white house with lawn and blue sky" style="background:linear-gradient(180deg,#7fb2d8 0%,#cfe2ee 45%,#6f9a4a 75%,#4f7d33 100%)"><span class="tag sale">For Sale</span></div>
    <div class="card-body">
      <h3>BILL TOWER, SURVEY, LA</h3>
      <div class="price">$990,985</div>
      <div class="spec"><svg viewBox="0 0 18 16"><path d="M1 8 H17 V11 Q17 14 14 14 H4 Q1 14 1 11 Z M3 8 V2 H6" fill="none" stroke="#999" stroke-width="1.4"/></svg>Bathrooms<b>2</b></div>
      <div class="spec"><svg viewBox="0 0 18 16"><path d="M1 4 V14 M1 10 H17 V14 M5 10 V7 H16 V10" fill="none" stroke="#999" stroke-width="1.4"/></svg>Beds<b>2</b></div>
      <div class="spec"><svg viewBox="0 0 18 16"><path d="M1 6 L9 1 L17 6 V15 H1 Z M4 9 H14 M4 12 H14" fill="none" stroke="#999" stroke-width="1.4"/></svg>Garages<b>1</b></div>
    </div>
  </article>

  <article class="card" style="left:458px">
    <div class="card-img" role="img" aria-label="Suburban home with driveway and garden" style="background:linear-gradient(180deg,#9ec3e0 0%,#e6ddc8 45%,#c9b79a 65%,#6e9a45 100%)"><span class="tag rent">For Rent</span></div>
    <div class="card-body">
      <h3>BILL TOWER, SURVEY, LA</h3>
      <div class="price">$990/MO</div>
      <div class="spec"><svg viewBox="0 0 18 16"><path d="M1 8 H17 V11 Q17 14 14 14 H4 Q1 14 1 11 Z M3 8 V2 H6" fill="none" stroke="#999" stroke-width="1.4"/></svg>Bathrooms<b>2</b></div>
      <div class="spec"><svg viewBox="0 0 18 16"><path d="M1 4 V14 M1 10 H17 V14 M5 10 V7 H16 V10" fill="none" stroke="#999" stroke-width="1.4"/></svg>Beds<b>2</b></div>
      <div class="spec"><svg viewBox="0 0 18 16"><path d="M1 6 L9 1 L17 6 V15 H1 Z M4 9 H14 M4 12 H14" fill="none" stroke="#999" stroke-width="1.4"/></svg>Garages<b>1</b></div>
    </div>
  </article>

  <article class="card" style="left:780px">
    <div class="card-img" role="img" aria-label="Modern living room with white sofa and large windows" style="background:linear-gradient(135deg,#3a3a3a 0%,#6c6c6c 40%,#d8d2c8 70%,#f1efe9 100%)"><span class="tag sale">For Sale</span></div>
    <div class="card-body">
      <h3>BILL TOWER, SURVEY, LA</h3>
      <div class="price">$990,985</div>
      <div class="spec"><svg viewBox="0 0 18 16"><path d="M1 8 H17 V11 Q17 14 14 14 H4 Q1 14 1 11 Z M3 8 V2 H6" fill="none" stroke="#999" stroke-width="1.4"/></svg>Bathrooms<b>2</b></div>
      <div class="spec"><svg viewBox="0 0 18 16"><path d="M1 4 V14 M1 10 H17 V14 M5 10 V7 H16 V10" fill="none" stroke="#999" stroke-width="1.4"/></svg>Beds<b>2</b></div>
      <div class="spec"><svg viewBox="0 0 18 16"><path d="M1 6 L9 1 L17 6 V15 H1 Z M4 9 H14 M4 12 H14" fill="none" stroke="#999" stroke-width="1.4"/></svg>Garages<b>1</b></div>
    </div>
  </article>
</section>

<section class="testimonials">
  <h2 class="section-head"><span class="chev">‹</span>WHAT CLIENT SAY<span class="chev">›</span></h2>
  <p class="quote">A wonderful serenity has taken possession of my entire soul, like these sweet mornings of spring which I enjoy with my whole heart.<br>I am alone, and feel the charm of existence in this spot, which was created for the bliss of souls like mine.</p>
  <div class="avatar" role="img" aria-label="Client portrait"></div>
  <p class="client">John Doe</p>
</section>

<section class="contact" aria-label="Contact">
  <h2 style="left:134px">IT’S EASY TO FIND US</h2>
  <h2 style="left:524px">QUICK CONTACT</h2>

  <div class="info" style="top:104px"><span class="pin"><svg width="20" height="24" viewBox="0 0 20 24"><path d="M10 1 Q18 1 18 9 Q18 15 10 23 Q2 15 2 9 Q2 1 10 1 Z" fill="#fff"/><circle cx="10" cy="9" r="3" fill="#a8dc4a"/></svg></span><div><h4>ADDRESS</h4><p>#2868 Lorem ipsum dolor sit amet, consectetur<br>adipiscing elit</p></div></div>
  <div class="info" style="top:192px"><span class="pin"><svg width="22" height="22" viewBox="0 0 22 22"><path d="M5 2 L9 7 L7 10 Q9 14 12 15 L15 13 L20 17 L17 21 Q8 20 1 6 Z" fill="#fff"/></svg></span><div><h4>PHONE</h4><p>(555) 210-4410, (555) 210-4411, (555) 210-4412</p></div></div>
  <div class="info" style="top:276px"><span class="pin"><svg width="24" height="18" viewBox="0 0 24 18"><rect x="1" y="1" width="22" height="16" fill="#fff"/><polyline points="1,1 12,10 23,1" fill="none" stroke="#a8dc4a" stroke-width="2"/></svg></span><div><h4>EMAIL</h4><p>info@lanterndwelling.test, hello@lanterndwelling.test</p></div></div>

  <div class="input" style="left:530px;top:106px;width:262px;height:38px">Name</div>
  <div class="input" style="left:804px;top:106px;width:264px;height:38px">Email</div>
  <div class="input" style="left:530px;top:156px;width:538px;height:128px">Message</div>
  <div class="btn-submit">Submit</div>

  <div class="socials"><span></span><span></span><span></span></div>
  <p class="copyright">© 2016 Lantern Dwelling. All Right Reserved</p>
</section>

</body>
</html>
```